Business Card Design

Lawyer
Business name "HarlowLaw"
Areas of expertise:
property
commercial
trusts
immigration
franchising
I want the following quote on the back of the card somewhere.
"Education is when you read the fine print,
experience is what you get if you don't." Dirk Vanholm
Probably the "areas of expertise" should be on the back also to avoid cluttering the front.
As for colours, I like the shades of blue used on qvelbank.com.
The basic part of the card with the contact info needs to be white and uncluttered.
Target Market(s)
small to medium sized self employed business people
Industry/Entity Type
Business
Contact Information for Business Card
Glen Harlow
Phone + 64 9 514 6937
Fax: + 64 9 514 6936
PO Box 734
Marrowvale
Kestonby 4417
NZ
email: glen@fernmarklaw.co.nz

```html
<!DOCTYPE html>
<html lang="en">
<head>
<meta charset="utf-8">
<title>HarlowLaw Business Card</title>
<link rel="stylesheet" href="https://fonts.googleapis.com/css2?family=Open+Sans:ital,wght@0,300;0,400;0,600;0,700;1,400;1,600&display=swap">
<style>
  :root {
    --page: #e9e6e1;
    --cyan-light: #27c3e0;
    --cyan: #169ccb;
    --blue: #0f73ab;
    --blue-deep: #0a568c;
    --ink: #ffffff;
    --ink-soft: #e6f6fb;
    --icon-bg: #f2f7fa;
    --icon-ink: #0d5f96;
  }
  * { box-sizing: border-box; margin: 0; padding: 0; }
  html, body {
    width: 1200px; height: 902px; overflow: hidden;
    background: var(--page);
    font-family: "Open Sans", Arial, sans-serif;
  }
  .canvas { position: relative; width: 1200px; height: 902px; }
  .card {
    position: absolute; top: 101px;
    width: 400px; height: 700px;
    border-radius: 6px; overflow: hidden;
    box-shadow: 0 10px 24px rgba(0,0,0,0.18);
    color: var(--ink);
  }
  .card--back { left: 150px; }
  .card--front { left: 650px; }
  .card__surface { position: absolute; inset: 0; width: 100%; height: 100%; }

  /* Back side */
  .quote {
    position: absolute; top: 44px; right: 30px; width: 340px;
    text-align: right; font-style: italic; font-size: 15px; line-height: 1.45;
    color: var(--ink-soft);
  }
  .quote__author { display: block; margin-top: 2px; font-weight: 600; }
  .brand {
    position: absolute; top: 250px; left: 0; right: 0;
    text-align: center; font-size: 32px; font-weight: 700; letter-spacing: 0.2px;
  }
  .expertise { position: absolute; top: 345px; left: 80px; }
  .expertise__title { font-size: 19px; font-weight: 600; margin-bottom: 14px; margin-left: 10px; }
  .expertise__list { list-style: none; font-size: 19px; font-weight: 600; line-height: 1.3; }
  .expertise__list li:nth-child(1) { margin-left: 24px; }
  .expertise__list li:nth-child(2) { margin-left: 18px; }
  .expertise__list li:nth-child(3) { margin-left: 12px; }
  .expertise__list li:nth-child(4) { margin-left: 6px; }
  .expertise__list li::before { content: "* "; }

  /* Front side */
  .identity { position: absolute; top: 120px; right: 34px; text-align: right; }
  .identity__name { font-size: 34px; font-weight: 300; line-height: 1.1; }
  .identity__name strong { font-weight: 700; }
  .identity__role { font-size: 21px; font-weight: 600; margin-right: 40px; }
  .contacts { position: absolute; top: 390px; left: 36px; right: 24px; list-style: none; }
  .contacts__item {
    display: flex; align-items: center; gap: 18px;
    height: 46px; font-size: 15px; color: var(--ink-soft);
    white-space: nowrap;
  }
  .contacts__icon {
    width: 28px; height: 28px; border-radius: 50%;
    background: var(--icon-bg); flex: none;
    display: flex; align-items: center; justify-content: center;
    box-shadow: 0 1px 3px rgba(0,0,0,0.3);
  }
  .contacts__icon svg { width: 16px; height: 16px; fill: var(--icon-ink); }
</style>
</head>
<body>
<main class="canvas">

  <section class="card card--back" aria-label="Card back">
    <svg class="card__surface" viewBox="0 0 400 700" preserveAspectRatio="none" aria-hidden="true">
      <defs>
        <linearGradient id="backTop" x1="0" y1="0" x2="0.6" y2="1">
          <stop offset="0" stop-color="#1a9fcc"/>
          <stop offset="0.6" stop-color="#22bddc"/>
          <stop offset="1" stop-color="#1791c4"/>
        </linearGradient>
        <linearGradient id="backBottom" x1="0" y1="0" x2="0" y2="1">
          <stop offset="0" stop-color="#0f73ab"/>
          <stop offset="1" stop-color="#0a568c"/>
        </linearGradient>
      </defs>
      <rect width="400" height="700" fill="url(#backBottom)"/>
      <polygon points="0,0 400,0 400,330 0,230" fill="url(#backTop)"/>
      <polygon points="150,0 400,0 400,150" fill="#ffffff" opacity="0.08"/>
      <polygon points="0,0 200,0 0,170" fill="#0a568c" opacity="0.18"/>
      <polygon points="0,230 400,330 400,400 0,270" fill="#169ccb" opacity="0.45"/>
      <polygon points="220,0 400,0 400,330 300,280" fill="#ffffff" opacity="0.05"/>
    </svg>
    <blockquote class="quote">
      "Education is when you read the fine print, experience is what you get if you don't."
      <span class="quote__author">Dirk Vanholm</span>
    </blockquote>
    <h1 class="brand">HarlowLaw</h1>
    <div class="expertise">
      <p class="expertise__title">"areas of expertise"</p>
      <ul class="expertise__list">
        <li>Trusts</li>
        <li>Property</li>
        <li>Franchising</li>
        <li>Commercial</li>
        <li>Immigration</li>
      </ul>
    </div>
  </section>

  <section class="card card--front" aria-label="Card front">
    <svg class="card__surface" viewBox="0 0 400 700" preserveAspectRatio="none" aria-hidden="true">
      <defs>
        <linearGradient id="frontTop" x1="0" y1="0" x2="0.5" y2="1">
          <stop offset="0" stop-color="#27c3e0"/>
          <stop offset="1" stop-color="#1595c6"/>
        </linearGradient>
        <linearGradient id="frontBottom" x1="0" y1="0" x2="0" y2="1">
          <stop offset="0" stop-color="#0e6ca5"/>
          <stop offset="1" stop-color="#0a568c"/>
        </linearGradient>
      </defs>
      <rect width="400" height="700" fill="url(#frontBottom)"/>
      <polygon points="0,0 400,0 400,330 0,270" fill="url(#frontTop)"/>
      <polygon points="0,0 260,0 0,140" fill="#ffffff" opacity="0.1"/>
      <polygon points="260,0 400,0 400,200" fill="#0a568c" opacity="0.12"/>
      <polygon points="0,270 400,330 400,380 0,300" fill="#169ccb" opacity="0.4"/>
      <polygon points="0,300 400,380 400,700 0,700" fill="#ffffff" opacity="0.03"/>
    </svg>
    <div class="identity">
      <h2 class="identity__name">Glen <strong>Harlow</strong></h2>
      <p class="identity__role">Lawyer</p>
    </div>
    <ul class="contacts">
      <li class="contacts__item">
        <span class="contacts__icon"><svg viewBox="0 0 16 16" aria-label="Phone"><path d="M3 2h3l1 3-2 1.2a8 8 0 0 0 4.8 4.8L11 9l3 1v3a1 1 0 0 1-1 1A12 12 0 0 1 2 3a1 1 0 0 1 1-1z"/></svg></span>
        + 64 9 514 6937
      </li>
      <li class="contacts__item">
        <span class="contacts__icon"><svg viewBox="0 0 16 16" aria-label="Fax"><path d="M4 1h8v4H4zM2 6h12v6h-2V9H4v3H2zM5 10h6v5H5z"/></svg></span>
        + 64 9 514 6936
      </li>
      <li class="contacts__item">
        <span class="contacts__icon"><svg viewBox="0 0 16 16" aria-label="Email"><path d="M1 3h14v1.5L8 9 1 4.5zM1 6l7 4.5L15 6v7H1z"/></svg></span>
        glen@fernmarklaw.co.nz
      </li>
      <li class="contacts__item">
        <span class="contacts__icon"><svg viewBox="0 0 16 16" aria-label="Address"><path d="M8 1l7 6.5h-2V15H9.5v-4h-3v4H3V7.5H1z"/></svg></span>
        PO Box 734 Marrowvale Kestonby 4417 NZ
      </li>
    </ul>
  </section>

</main>
</body>
</html>
```